Kestrel Home Business Card Design

We need a business card for a Building company based in Queensland, Australia. Our colours are orange black and we do base all our homes design names and other aspect of our business on astrology. We want the consumer to perceive the company as professional and to attract investors to our company.We have over 20 years in the building industry.We pride ourselves on our innovation of designs and making the building process for anyone from families to investor a smooth and simple experience.
Business
Amelia Prichard0411752116PO Box 454, Mudgeerbaameliaprichard@zodiachomes.com

```html
<!DOCTYPE html>
<html lang="en">
<head>
<meta charset="utf-8">
<title>Kestrel Homes Business Card</title>
<link rel="stylesheet" href="https://fonts.googleapis.com/css2?family=Montserrat:ital,wght@0,500;0,600;0,700;1,500&display=swap">
<style>
  :root {
    --orange: #f7941d;
    --charcoal: #3b3b3b;
    --ink: #1f1f1f;
    --paper: #ffffff;
    --trim: #e0242a;
    --photo-sky: #8fa6c4;
    --photo-ground: #6e8a4a;
  }
  html, body {
    margin: 0;
    padding: 0;
    width: 691px;
    height: 1200px;
    overflow: hidden;
    background: var(--paper);
    font-family: "Montserrat", sans-serif;
  }
  .canvas {
    position: relative;
    width: 691px;
    height: 1200px;
  }
  .card {
    position: absolute;
    left: 157px;
    width: 392px;
    height: 237px;
    outline: 1px solid var(--trim);
  }
  .card--front { top: 136px; }
  .card--back { top: 396px; }
  .card svg { display: block; }
  .brand-title { font-family: "Montserrat", sans-serif; font-weight: 700; fill: var(--ink); }
  .seal-name { font-family: "Montserrat", sans-serif; font-weight: 700; fill: var(--paper); }
  .holder-name { font-family: "Montserrat", sans-serif; font-weight: 600; fill: var(--paper); }
  .contact-line { font-family: "Montserrat", sans-serif; font-style: italic; font-weight: 500; fill: var(--paper); }
  .badge-text { font-family: "Montserrat", sans-serif; font-weight: 600; fill: var(--paper); }
</style>
</head>
<body>
<main class="canvas">

  <!-- Front of card -->
  <section class="card card--front" aria-label="Business card front">
    <svg width="392" height="237" viewBox="0 0 392 237">
      <defs>
        <linearGradient id="house-photo" x1="0" y1="0" x2="0" y2="1">
          <stop offset="0" stop-color="var(--photo-sky)"/>
          <stop offset="0.55" stop-color="#8a8178"/>
          <stop offset="1" stop-color="var(--photo-ground)"/>
        </linearGradient>
      </defs>
      <rect class="card-body" x="0" y="0" width="392" height="237" fill="var(--charcoal)"/>
      <rect class="title-band" x="0" y="0" width="392" height="49" fill="var(--paper)"/>
      <text class="brand-title" x="21" y="44" font-size="23">Kestrel Homes</text>

      <rect class="house-photo" role="img" aria-label="Photo of a single-storey brick home with garage and front garden" x="1" y="49" width="243" height="150" fill="url(#house-photo)"/>

      <path class="wave-orange" d="M0,168 C60,146 120,196 205,183 C275,172 320,178 392,164 L392,237 L0,237 Z" fill="var(--orange)"/>
      <path class="swoop-white" d="M0,196 C70,176 150,214 235,198 C300,186 350,172 392,170" fill="none" stroke="var(--paper)" stroke-width="5"/>
      <path class="swoop-black" d="M0,206 C80,190 150,222 240,208 C300,198 350,186 392,184" fill="none" stroke="var(--ink)" stroke-width="3"/>
      <path class="swoop-white-upper" d="M250,180 C300,168 340,162 392,150" fill="none" stroke="var(--paper)" stroke-width="4"/>

      <g class="brand-seal">
        <circle cx="291" cy="104" r="60" fill="var(--orange)"/>
        <text class="seal-name" x="291" y="108" font-size="11" text-anchor="middle">Kestrel Homes</text>
      </g>

      <g class="experience-badge">
        <circle cx="328" cy="196" r="9" fill="none" stroke="var(--paper)" stroke-width="1.5"/>
        <text class="badge-text" x="328" y="196" font-size="6" text-anchor="middle">20</text>
        <text class="badge-text" x="328" y="202" font-size="4" text-anchor="middle">YEARS</text>
        <text class="badge-text" x="328" y="224" font-size="5.5" text-anchor="middle">IN THE BUILDING INDUSTRY</text>
      </g>
    </svg>
  </section>

  <!-- Back of card -->
  <section class="card card--back" aria-label="Business card back">
    <svg width="392" height="237" viewBox="0 0 392 237">
      <defs>
        <linearGradient id="house-shade" x1="0" y1="0" x2="0" y2="1">
          <stop offset="0" stop-color="#444444"/>
          <stop offset="1" stop-color="#343434"/>
        </linearGradient>
      </defs>
      <rect class="card-body" x="0" y="0" width="392" height="237" fill="var(--charcoal)"/>
      <rect class="house-backdrop" role="img" aria-label="Faint darkened photo of a home facade" x="0" y="51" width="392" height="130" fill="url(#house-shade)"/>
      <rect class="top-strip" x="0" y="0" width="392" height="16" fill="var(--charcoal)"/>
      <rect class="title-band" x="0" y="16" width="392" height="35" fill="var(--paper)"/>
      <text class="brand-title" x="371" y="44" font-size="21" text-anchor="end">Kestrel Homes</text>

      <g class="brand-seal">
        <circle cx="73" cy="82" r="55" fill="var(--orange)"/>
        <text class="seal-name" x="73" y="86" font-size="10" text-anchor="middle">Kestrel Homes</text>
      </g>

      <path class="wave-orange" d="M0,170 C50,158 85,200 165,205 C245,210 320,192 392,180 L392,237 L0,237 Z" fill="var(--orange)"/>
      <path class="swoop-white" d="M0,178 C50,168 90,208 170,212 C250,216 320,198 392,190" fill="none" stroke="var(--paper)" stroke-width="4"/>
      <path class="swoop-black" d="M0,188 C60,178 100,216 180,220 C260,222 320,208 392,200" fill="none" stroke="var(--ink)" stroke-width="3"/>

      <text class="holder-name" x="54" y="165" font-size="14">Harriet Colvane</text>
      <line class="divider" x1="178" y1="139" x2="178" y2="185" stroke="var(--paper)" stroke-width="1.2"/>

      <g class="contact-icons" fill="var(--paper)">
        <rect x="189" y="141" width="6" height="10" rx="1.2" fill="none" stroke="var(--paper)" stroke-width="1.2"/>
        <rect x="188" y="156" width="9" height="7" rx="1" fill="none" stroke="var(--paper)" stroke-width="1.1"/>
        <path d="M188,161 L192.5,159 L197,161" fill="none" stroke="var(--paper)" stroke-width="0.9"/>
        <path d="M187.5,176 L192.5,171 L197.5,176 L196,176 L196,180 L189,180 L189,176 Z"/>
      </g>
      <text class="contact-line" x="201" y="150" font-size="8.2">0487309625</text>
      <text class="contact-line" x="201" y="164" font-size="8.2">harrietcolvane@kestrelhomes.example</text>
      <text class="contact-line" x="201" y="179" font-size="8.2">PO Box 872, Corrowin QLD 4213</text>
    </svg>
  </section>

</main>
</body>
</html>
```